Systems and Technology Consultants - Website

Design & Build a website for a new company which operates in the Systems and Technology space for Transportation, Government and Commercial sectors.

Overall design should be minimalist in nature.
Should also have a feed that provides news and event updates on the main page.
Logo has already been awarded and should be incorporated into the site.

We like the overall layout, functionality and simplicity of the below sites. Submitted designs could be similar to or a combination of the aspects on these sites, or perhaps a whole different concept - we are open to new ideas.
Norvique.com
Teblo.it

Update 1 Dated 27 May 2014

All I am moving away from the Teblo.it website and would like it to be more aligned with Norvique.com not only in layout but in functionality. I will be extending the deadline of this design brief for two weeks to incorporate additional requirements and will add addtional funding to the project.

Apologies for not having more information available to provide but with so many submissions its getting confusing.

Thanks Derek

Please note that the brief has been updated and the deadline has been extended.

Important: We will need two language versions of the website, English and Arabic; the website is hosted on HostPelican

Hello All, Thank you for your submissions. We have narrowed it down to the final 6 designers and I just wanted to take a moment and provide a bit of feedback regarding the concepts that we like and the modifications we are looking for. First, let me mention some of the design functions we like. - At the top of the homepage we really like the "region" or "language" tab so that the website can be viewed in both English and Arabic. - We like the homepage to have clear color variation so that the different sections of the homepage are distinct. Additionally, we like the bottom portion of the homepage to be in red. We feel that draws attention to our contact information. Again, we would like the colors to integrate black, gray-scale, red, etc. - Having a search tab at the top of the home page, or integrated into the main image, so that the site is easy to navigate. - We especially like the main image to have the scrolling tabs at the bottom so it is easy to browse the services offered (Consultancy, Solutions Architecture, Masters Systems Integration, Independent Design Review). - In regards to the services offered tab we really like the idea that a few people presented that have the outside of our logo with an icon in the middle of consultancy, solutions, etc., etc. Secondly, as mentioned in our brief we really enjoy the design of norvique site. Specially, we enjoy the strong iconic images they use, the way the tabs at the top scroll easily, and contact us page that generates an email. Lastly, I've included some photos of the concept we have been working on. What we are trying to demonstrate is how our company offers a range of services that are essentially linked together. We provide individual services that when combined present the full service package. We would like this concept to be integrated into the over concept of our website. Please feel free to ask for clarification of any of the above points or contact us if you have any additional questions. We appreciate all of your hard work and are very excited to see the updated designs. Best, Marta Vennick Quelbrant Senior Program Manager marta.vennick@quelbrant-example.com

Industry/Entity Type

Government

Font styles to use
Serif
Sans Serif

Requirements
Must have
• Must work on/adapt to various/mobile devices (responsive)
Must be simple and straightforward
Colors should be in line/matching with logo
2 language versions: English and Arabic (no Thai)
Services should be the first group/row of items after/below the main image
Note: the website will be hosted by hostpelican
Nice to have
• Submit feedback form
What's New section
The banner at the bottom of the site should not be too large; we would like a narrow one more
It would be nice if the header/top banner (with Home, About, etc. tabs) could stay in place as you scroll down (like Norvique and Chatterloop)
We will likely only use one image with a Company slogan on the Home page rather than a carousel of images to rotate through
Should not have
• This is the existing website: http://www.quelbrant-example.org
We do not like the animation, the way the banner icons/titles bounce
Not simple enough, we don't like the functionality or how pages load so slowly
We do not like the logo centered - it should be at the left
The banner and its tabs should not be towards the right, we would like them to be centered, to go all the way across and to be below the logo

```html
<!DOCTYPE html>
<html lang="en">
<head>
<meta charset="utf-8">
<title>Quelbrant – System Professionals</title>
<link rel="stylesheet" href="https://fonts.googleapis.com/css2?family=Roboto:wght@300;400;500;700&display=swap">
<style>
:root{
  --red:#ed1c24;
  --red-dark:#c8151c;
  --ink:#333;
  --muted:#888;
  --line:#e2e2e2;
  --card:#f3f3f3;
  --footer:#333;
  --white:#fff;
}
*{box-sizing:border-box;margin:0;padding:0}
html,body{width:731px;height:1200px;overflow:hidden;background:var(--white)}
body{font-family:"Roboto",Arial,sans-serif;color:var(--ink);position:relative}
a{color:inherit;text-decoration:none}

/* Header */
.site-header{position:absolute;left:0;top:0;width:731px;height:85px}
.brand{position:absolute;left:78px;top:33px;display:flex;align-items:center;gap:7px}
.brand-square{width:14px;height:14px;background:var(--red)}
.brand-name{font-size:16px;font-weight:500;color:var(--ink)}
.main-nav{position:absolute;left:241px;top:35px;display:flex;align-items:center}
.main-nav a{font-size:8.6px;color:#444;padding:0 9px;border-left:1px solid var(--line);line-height:15px;text-transform:uppercase}
.main-nav a.is-active{background:var(--red);color:var(--white);border:none;padding:0 6px;margin-right:6px}
.main-nav a.is-active + a{border-left:none}
.search-btn{position:absolute;left:637px;top:35px;width:15px;height:15px;background:var(--red)}

/* Hero */
.hero{position:absolute;left:0;top:85px;width:731px;height:305px;
  background:radial-gradient(ellipse 220px 70px at 230px 80px,rgba(200,30,30,.75),transparent),
             radial-gradient(ellipse 200px 150px at 620px 110px,rgba(90,100,110,.6),transparent),
             linear-gradient(180deg,#3d2a2a 0%,#262021 55%,#1b1b1d 100%);
  color:var(--white);text-align:center}
.hero-title{position:absolute;top:98px;width:100%;font-size:29px;font-weight:700;letter-spacing:.2px}
.hero-text{position:absolute;top:157px;left:90px;width:551px;font-size:14.5px;line-height:22px;font-weight:400}

/* Services */
.services{position:absolute;left:78px;top:427px;width:573px;height:130px;background:var(--red);display:flex}
.service{flex:1;border-left:1px solid var(--red-dark);text-align:center;color:var(--white);padding-top:17px}
.service:first-child{border-left:none}
.service svg{width:20px;height:20px;display:block;margin:0 auto}
.service h3{font-size:10px;font-weight:500;margin:13px 0 15px}
.service p{font-size:7.8px;line-height:11px;padding:0 8px;font-weight:400}

/* Section heads */
.section-head{position:absolute;display:flex;justify-content:space-between;align-items:baseline;border-bottom:1px solid var(--line);padding-bottom:8px}
.section-head h2{font-size:11px;font-weight:500;color:#333}
.section-head a{font-size:7.5px;color:var(--muted)}

/* News */
.news{position:absolute;left:79px;top:629px;display:flex;gap:13px}
.news-card{width:133px;height:194px;background:var(--card);text-align:center}
.news-photo{height:72px}
.news-card h3{font-size:10.5px;font-weight:500;margin:10px 0 9px}
.news-card p{font-size:7.8px;line-height:11px;color:var(--muted);padding:0 11px}
.btn{display:inline-block;margin-top:8px;background:var(--red);color:var(--white);font-size:8px;font-weight:500;padding:4px 10px}

/* Events */
.event{position:absolute;left:78px;display:flex}
.event-date{width:38px;height:42px;background:var(--card);border-bottom:2px solid var(--red);text-align:center;padding-top:4px;color:#555}
.event-date b{display:block;font-size:10.5px;font-weight:500}
.event-date span{display:block;font-size:7.5px;line-height:9px;color:var(--muted)}
.event-body{margin-left:10px;width:235px}
.event-body h3{font-size:10.5px;font-weight:500;margin-top:-2px}
.event-body p{font-size:7.7px;line-height:12px;color:var(--muted);margin-top:6px}

/* Testimonial */
.quote{position:absolute;left:371px;top:895px;width:281px;height:97px;background:var(--card);padding:6px 7px;font-size:7.7px;line-height:12px;color:var(--muted)}
.quote::after{content:"";position:absolute;left:42px;bottom:-7px;border:7px solid transparent;border-bottom:0;border-top-color:var(--card)}
.slider-arrows{position:absolute;left:628px;top:860px;display:flex;gap:2px}
.slider-arrows span{width:11px;height:11px;border-radius:3px;background:#c9c9c9}
.author{position:absolute;left:395px;top:1014px;display:flex;align-items:center}
.author-photo{width:44px;height:44px}
.author-name{margin-left:13px;font-size:8px;color:#555}
.author-name b{font-weight:500;color:#333}

/* Footer */
.site-footer{position:absolute;left:0;top:1094px;width:731px;height:106px;background:var(--footer);color:#ddd;text-align:center}
.footer-nav{display:flex;justify-content:center;margin-top:20px}
.footer-nav a{font-size:8.6px;padding:0 12px;border-left:1px solid #555;line-height:14px;text-transform:uppercase}
.footer-nav a:first-child{border-left:none}
.copyright{font-size:8px;margin-top:19px}
.social{display:flex;justify-content:center;gap:6px;margin-top:9px}
.social span{width:14px;height:14px;border-radius:50%;background:#bbb}
</style>
</head>
<body>

<header class="site-header">
  <a class="brand" href="#">
    <span class="brand-square"></span>
    <span class="brand-name">Quelbrant</span>
  </a>
  <nav class="main-nav">
    <a class="is-active" href="#">Home</a>
    <a href="#">Business Unit</a>
    <a href="#">Services</a>
    <a href="#">About Us</a>
    <a href="#">Locations</a>
    <a href="#">Contact Us</a>
  </nav>
  <a class="search-btn" href="#" aria-label="Search">
    <svg viewBox="0 0 15 15" width="15" height="15"><circle cx="6.5" cy="6.5" r="2.8" fill="none" stroke="#fff" stroke-width="1.4"/><line x1="8.6" y1="8.6" x2="11.5" y2="11.5" stroke="#fff" stroke-width="1.6"/></svg>
  </a>
</header>

<section class="hero" role="img" aria-label="Blurred close-up of red and yellow network cables in a server rack">
  <h1 class="hero-title">SYSTEM PROFESSIONALS</h1>
  <p class="hero-text">We provide construction management, engineering, design services and turn-key solutions for technical systems.</p>
</section>

<section class="services">
  <div class="service">
    <svg viewBox="0 0 20 20"><circle cx="10" cy="6" r="4.5" fill="#fff"/><path d="M2 19c0-5 4-7 8-7s8 2 8 7z" fill="#fff"/></svg>
    <h3>Consulting</h3>
    <p>Lorem ipsum dolor sit amet, consectetur adipisicing elit sed do eiusmod tempor.</p>
  </div>
  <div class="service">
    <svg viewBox="0 0 20 20"><circle cx="10" cy="10" r="7" fill="none" stroke="#fff" stroke-width="4" stroke-dasharray="3 2.5"/><circle cx="10" cy="10" r="4" fill="none" stroke="#fff" stroke-width="2.5"/></svg>
    <h3>Engineering</h3>
    <p>Lorem ipsum dolor sit amet, consectetur adipisicing elit sed do eiusmod tempor.</p>
  </div>
  <div class="service">
    <svg viewBox="0 0 20 20"><path d="M4 16 L14 6 M6 4 L16 14" stroke="#fff" stroke-width="2.6" stroke-linecap="round"/><rect x="12" y="2" width="6" height="4" fill="#fff" transform="rotate(45 15 4)"/></svg>
    <h3>Construction</h3>
    <p>Lorem ipsum dolor sit amet, consectetur adipisicing elit sed do eiusmod tempor.</p>
  </div>
  <div class="service">
    <svg viewBox="0 0 20 20"><circle cx="10" cy="10" r="7" fill="none" stroke="#fff" stroke-width="2" stroke-dasharray="7 4"/><circle cx="10" cy="3" r="2" fill="#fff"/><circle cx="16" cy="13" r="2" fill="#fff"/><circle cx="4" cy="13" r="2" fill="#fff"/></svg>
    <h3>Operations</h3>
    <p>Lorem ipsum dolor sit amet, consectetur adipisicing elit sed do eiusmod tempor.</p>
  </div>
  <div class="service">
    <svg viewBox="0 0 20 20"><rect x="3" y="2" width="14" height="4.5" fill="#fff"/><rect x="3" y="8" width="14" height="4.5" fill="#fff"/><rect x="3" y="14" width="14" height="4.5" fill="#fff"/></svg>
    <h3>Maintenance</h3>
    <p>Lorem ipsum dolor sit amet, consectetur adipisicing elit sed do eiusmod tempor.</p>
  </div>
</section>

<div class="section-head" style="left:78px;top:591px;width:573px">
  <h2>Latest News</h2><a href="#">View all</a>
</div>

<section class="news">
  <article class="news-card">
    <div class="news-photo" role="img" aria-label="Portrait of a businessman in a suit by a window" style="background:linear-gradient(90deg,#e4e4e4,#8a8a8a)"></div>
    <h3>Lorem Ipsum</h3>
    <p>Lorem ipsum dolor sit amet, consectetur adipisicing elit, sed do eiusmod tempor incidi-dunt ut labore et dolore magna aliqua.</p>
    <a class="btn" href="#">Read more</a>
  </article>
  <article class="news-card">
    <div class="news-photo" role="img" aria-label="Presenter speaking to a seated audience" style="background:linear-gradient(90deg,#5c6a55,#a9b7c4 50%,#7d6a5a)"></div>
    <h3>Lorem Ipsum</h3>
    <p>Lorem ipsum dolor sit amet, consectetur adipisicing elit, sed do eiusmod tempor incidi-dunt ut labore et dolore magna aliqua.</p>
    <a class="btn" href="#">Read more</a>
  </article>
  <article class="news-card">
    <div class="news-photo" role="img" aria-label="Colleagues in a bright office meeting" style="background:linear-gradient(90deg,#d8c59c,#e9ecef 50%,#9db0c7)"></div>
    <h3>Lorem Ipsum</h3>
    <p>Lorem ipsum dolor sit amet, consectetur adipisicing elit, sed do eiusmod tempor incidi-dunt ut labore et dolore magna aliqua.</p>
    <a class="btn" href="#">Read more</a>
  </article>
  <article class="news-card">
    <div class="news-photo" role="img" aria-label="Group of business people applauding" style="background:linear-gradient(90deg,#4a3a35,#a07a62 50%,#3b3433)"></div>
    <h3>Lorem Ipsum</h3>
    <p>Lorem ipsum dolor sit amet, consectetur adipisicing elit, sed do eiusmod tempor incidi-dunt ut labore et dolore magna aliqua.</p>
    <a class="btn" href="#">Read more</a>
  </article>
</section>

<div class="section-head" style="left:78px;top:859px;width:282px">
  <h2>Event Updates</h2><a href="#">View all</a>
</div>

<article class="event" style="top:893px">
  <div class="event-date"><b>17</b><span>MAY</span><span>2014</span></div>
  <div class="event-body"><h3>Lorem Ipsum</h3><p>Lorem ipsum dolor sit amet, consectetur adipiscing elit. Nulla vehicula feugiat blandit. Nulla facilisi. Nulla tellus nisi...</p></div>
</article>
<article class="event" style="top:954px">
  <div class="event-date"><b>04</b><span>MAY</span><span>2014</span></div>
  <div class="event-body"><h3>Lorem Ipsum</h3><p>Lorem ipsum dolor sit amet, consectetur adipiscing elit. Nulla vehicula feugiat blandit. Nulla facilisi. Nulla tellus nisi...</p></div>
</article>
<article class="event" style="top:1014px">
  <div class="event-date"><b>23</b><span>APRIL</span><span>2014</span></div>
  <div class="event-body"><h3>Lorem Ipsum</h3><p>Lorem ipsum dolor sit amet, consectetur adipiscing elit. Nulla vehicula feugiat blandit. Nulla facilisi. Nulla tellus nisi...</p></div>
</article>

<div class="section-head" style="left:371px;top:859px;width:281px">
  <h2>What Clients Say</h2>
</div>
<div class="slider-arrows"><span></span><span></span></div>

<blockquote class="quote">Fusce ele mentum, nulla vel pellentesque consequat, ante nulla hen-drerit arcu, ac tincidunt mauris lacus sed leo. vamus suscipit molestie vestibulum.Fusce elementum, nulla vel pellentesque consequat, ante nulla hendrerit arcu, ac tincidunt mauris lacus sed leo. vamus suscipit molestie vestibulum.Fusce elementum, nulla vel pellentesque conse-quat, ante nulla hendrerit arcu, ac tincidunt mauris lacus sed leo. vamus suscipit molestie vestibulum.</blockquote>

<div class="author">
  <div class="author-photo" role="img" aria-label="Portrait of the company CEO" style="background:linear-gradient(135deg,#9a9a9a,#3a3a3a)"></div>
  <p class="author-name"><b>John Doe</b> - CEO Quelbrant</p>
</div>

<footer class="site-footer">
  <nav class="footer-nav">
    <a href="#">Home</a><a href="#">Business Unit</a><a href="#">Services</a><a href="#">About Us</a><a href="#">Locations</a><a href="#">Contact Us</a>
  </nav>
  <p class="copyright">Quelbrant © 2014 - All Rights Reserved</p>
  <div class="social"><span></span><span></span><span></span></div>
</footer>

</body>
</html>
```